Harbourline Electrical Solutions

On one side. LOGO (underneath:) Commercial Industrial Residential

- NAME & CONTACT DETAILS

Marcus T. Hollings
Project Manager

(Cell icon) (441) 555-0187
(Email icon) hlelectricalsolutions@mailvento.com
(Facebook & Instagram icons )@hlelectricalsolutions

Other side: LOGO - underneath ELECTRICAL CONSTRUCTION & MAINTENANCE . LED LIGHTING & AUTOMATION . LIFE SAFETY SYSTEMS (FIRE ALARM / SECURITY) . DATA & COMMUNICATION

```html
<!DOCTYPE html>
<html lang="en">
<head>
<meta charset="utf-8">
<title>Harbourline Electrical Solutions – Business Card</title>
<link href="https://fonts.googleapis.com/css2?family=Montserrat:wght@400;500;600;700&display=swap" rel="stylesheet">
<style>
  :root {
    --backdrop: #c9c9c9;
    --card-dark: #4a4a4b;
    --card-dark-text: #d4d4d4;
    --card-dark-brand: #d9d9d9;
    --card-light: #ffffff;
    --teal: #1f6f82;
    --navy-teal: #174f5e;
    --ink: #555a5e;
  }
  * { box-sizing: border-box; margin: 0; padding: 0; }
  html, body { width: 1200px; height: 960px; overflow: hidden; }
  body {
    background: var(--backdrop);
    font-family: "Montserrat", sans-serif;
    position: relative;
  }
  .card {
    position: absolute;
    left: 250px;
    width: 700px;
    height: 400px;
    border-radius: 22px;
    overflow: hidden;
    box-shadow: 0 10px 24px rgba(0,0,0,.25);
  }
  .brand-mark { width: 16px; height: 16px; background: currentColor; flex: none; }

  /* Back side */
  .card-back { top: 50px; background: var(--card-dark); }
  .card-back .brand {
    position: absolute; top: 135px; left: 0; right: 0;
    display: flex; justify-content: center; align-items: center; gap: 16px;
    color: var(--card-dark-brand);
  }
  .card-back .brand-name {
    font-size: 22px; font-weight: 600; letter-spacing: 2px;
    text-transform: uppercase; white-space: nowrap;
  }
  .services {
    position: absolute; top: 225px; left: 40px; right: 40px;
    text-align: center; color: var(--card-dark-text);
    font-size: 15px; line-height: 1.7; font-weight: 500;
  }

  /* Front side */
  .card-front { top: 510px; background: var(--card-light); }
  .card-front .swoosh { position: absolute; inset: 0; }
  .front-brand { position: absolute; top: 56px; left: 50px; color: var(--navy-teal); }
  .front-brand .brand-row { display: flex; align-items: center; gap: 10px; }
  .front-brand .brand-name {
    font-size: 18px; font-weight: 700; letter-spacing: 1px;
    text-transform: uppercase; white-space: nowrap;
  }
  .sectors {
    margin-top: 10px; font-size: 12px; font-weight: 500; letter-spacing: 1.5px;
    color: var(--ink); text-transform: uppercase;
  }
  .contact { position: absolute; left: 50px; top: 215px; }
  .person-name { font-size: 26px; font-weight: 700; color: var(--navy-teal); text-transform: uppercase; }
  .person-role { font-size: 15px; font-weight: 600; color: var(--ink); margin-top: 2px; }
  .contact-list { list-style: none; margin-top: 22px; font-size: 15px; color: var(--ink); }
  .contact-list li { display: flex; align-items: center; gap: 10px; margin-bottom: 8px; }
  .contact-list svg { width: 16px; height: 16px; fill: none; stroke: var(--navy-teal); stroke-width: 1.8; }
  .social {
    position: absolute; right: 24px; bottom: 34px;
    display: flex; align-items: center; gap: 7px;
    color: #fff; font-size: 12px; font-weight: 500; white-space: nowrap;
  }
  .social-dot { width: 10px; height: 10px; border-radius: 50%; background: #fff; flex: none; }
</style>
</head>
<body>

<section class="card card-back" aria-label="Card back">
  <div class="brand">
    <span class="brand-mark"></span>
    <span class="brand-name">Harbourline Electrical Solutions</span>
  </div>
  <p class="services">
    Electrical Construction &amp; Maintenance • LED Lighting &amp; Automation<br>
    Life Safety Systems (Fire Alarm / Security) • Data &amp; Communication
  </p>
</section>

<section class="card card-front" aria-label="Card front">
  <svg class="swoosh" viewBox="0 0 700 400" preserveAspectRatio="none" aria-hidden="true">
    <path d="M575 0 C655 120 630 280 470 400 L700 400 L700 0 Z" fill="var(--teal)"/>
    <path d="M530 0 C610 115 590 270 440 400" fill="none" stroke="var(--teal)" stroke-width="4"/>
  </svg>

  <div class="front-brand">
    <div class="brand-row">
      <span class="brand-mark"></span>
      <span class="brand-name">Harbourline Electrical Solutions</span>
    </div>
    <p class="sectors">Commercial • Industrial • Residential</p>
  </div>

  <div class="contact">
    <h1 class="person-name">Marcus T. Hollings</h1>
    <p class="person-role">Project Manager</p>
    <ul class="contact-list">
      <li>
        <svg viewBox="0 0 16 16"><rect x="4" y="1.5" width="8" height="13" rx="1.5"/><line x1="7" y1="12" x2="9" y2="12"/></svg>
        (441) 555-0187
      </li>
      <li>
        <svg viewBox="0 0 16 16"><rect x="1.5" y="3.5" width="13" height="9" rx="1"/><polyline points="1.5,4 8,9 14.5,4"/></svg>
        hlelectricalsolutions@mailvento.com
      </li>
    </ul>
  </div>

  <div class="social">
    <span class="social-dot"></span>
    <span>@hlelectricalsolutions</span>
  </div>
</section>

</body>
</html>
```